Quote Cards With KB May 2025 for Instagram

I would like to put these quotes over one of the pictures attached; Instagram (new size: 4:5 (1080 x 1350 pixels) One Quote per picture, and I want the quote to be bold or easy to read as well. I provided a few reference graphics that I really like as examples below. In very small letters at the bottom add @KBHarlowOnline

All of the pictures are attached; you can pick any photo and add one quote to it; but no stock photography

```html
<!DOCTYPE html>
<html lang="en">
<head>
<meta charset="utf-8">
<title>KB Quote Cards – May 2025</title>
<link href="https://fonts.googleapis.com/css2?family=Bebas+Neue&family=Nunito:wght@700&display=swap" rel="stylesheet">
<style>
  :root {
    --page-bg: #ededed;
    --magenta: #d10066;
    --footer-dark: #120509;
    --handle-pink: #ff4fa3;
    --quote-white: #ffffff;
  }
  * { box-sizing: border-box; margin: 0; padding: 0; }
  html, body {
    width: 1000px;
    height: 1200px;
    overflow: hidden;
    background: var(--page-bg);
  }
  .card-grid {
    position: relative;
    width: 1000px;
    height: 1200px;
    display: grid;
    grid-template-columns: 432px 432px;
    grid-template-rows: 540px 540px;
    column-gap: 40px;
    row-gap: 40px;
    padding: 40px 48px;
  }
  .quote-card {
    background: var(--magenta);
    padding: 6px;
    display: flex;
    flex-direction: column;
  }
  .quote-photo {
    height: 341px;
    flex: none;
  }
  .photo-hillside { background: linear-gradient(180deg, #b9d3ee 0%, #c7c9d6 35%, #8a7b6e 55%, #4a3b34 80%, #5a6a3a 100%); }
  .photo-kitchen-dark { background: linear-gradient(180deg, #5a2a20 0%, #7a3f30 40%, #2a1616 70%, #6a3a2c 100%); }
  .photo-kitchen-light { background: linear-gradient(180deg, #d8c3cf 0%, #e8dbe3 40%, #b896a8 70%, #5c3a4c 100%); }
  .photo-courtside { background: linear-gradient(160deg, #3a4a9a 0%, #8a5070 35%, #b05a98 55%, #2a1a24 80%, #1a1218 100%); }
  .quote-text {
    flex: 1;
    display: flex;
    align-items: center;
    justify-content: center;
    text-align: center;
    padding: 0 12px;
    font-family: "Bebas Neue", "Oswald", sans-serif;
    font-size: 24px;
    line-height: 28.5px;
    letter-spacing: 0.3px;
    color: var(--quote-white);
  }
  .card-footer {
    height: 48px;
    flex: none;
    background: var(--footer-dark);
    display: flex;
    align-items: center;
    justify-content: center;
  }
  .social-handle {
    font-family: "Nunito", sans-serif;
    font-weight: 700;
    font-size: 12.5px;
    color: var(--handle-pink);
  }
</style>
</head>
<body>
  <main class="card-grid">
    <article class="quote-card">
      <div class="quote-photo photo-hillside" role="img" aria-label="Photo of KB smiling in a black outfit, hand on hip, with hills and shrubs behind"></div>
      <p class="quote-text">You’re doing all the “right” things,<br>but your belly won’t go down?<br>Here’s what you haven’t tried.</p>
      <footer class="card-footer"><span class="social-handle">@KBHarlowOnline</span></footer>
    </article>

    <article class="quote-card">
      <div class="quote-photo photo-kitchen-dark" role="img" aria-label="Photo of KB in a sheer striped black top pointing down, in a wood-panelled kitchen"></div>
      <p class="quote-text">Your belly isn’t fat...<br>It’s hormonal. And here’s how to fix it.<br>Comment hormones if nothing is working.</p>
      <footer class="card-footer"><span class="social-handle">@KBHarlowOnline</span></footer>
    </article>

    <article class="quote-card">
      <div class="quote-photo photo-kitchen-light" role="img" aria-label="Photo of KB dancing in a white cropped sweater in a bright kitchen, pink tint"></div>
      <p class="quote-text">Tired. Moody.Stubborn belly fat.<br>Your hormones are screaming for help!<br>Let’s fix that.</p>
      <footer class="card-footer"><span class="social-handle">@KBHarlowOnline</span></footer>
    </article>

    <article class="quote-card">
      <div class="quote-photo photo-courtside" role="img" aria-label="Photo of KB courtside holding a basketball beside a friend taking a selfie, crowd behind"></div>
      <p class="quote-text">Bloating. Muffin top. Puffy waistline.<br>Your body’s screaming for a different<br>kind of fix. Here it is</p>
      <footer class="card-footer"><span class="social-handle">@KBHarlowOnline</span></footer>
    </article>
  </main>
</body>
</html>
```